Recipe Card Design

I have a small kitchen store in Livingston Montana, and I would like to have recipe cards (4x6 postcard) designed with my logo, lines for recipe writing, all in black and white. My website is here: www.brambleforkcookware.com

Store

```html
<!DOCTYPE html>
<html lang="en">
<head>
<meta charset="utf-8">
<title>Bramble Fork Cookware – Recipe Card</title>
<link href="https://fonts.googleapis.com/css2?family=Alfa+Slab+One&family=Poppins:wght@400&family=Cinzel:wght@600&display=swap" rel="stylesheet">
<style>
  :root {
    --ink: #111111;
    --rule: #2a2a2a;
    --faint: #e4e4e4;
    --paper: #ffffff;
  }
  html, body {
    margin: 0;
    padding: 0;
    overflow: hidden;
    background: var(--paper);
  }
  .card {
    position: relative;
    width: 1200px;
    height: 929px;
    background: var(--paper);
    overflow: hidden;
    color: var(--ink);
  }
  .cut-border {
    position: absolute;
    left: 40px;
    top: 40px;
    width: 1118px;
    height: 850px;
    box-sizing: border-box;
    border: 2px dashed var(--ink);
  }
  .backdrop-name {
    position: absolute;
    left: 300px;
    top: 110px;
    width: 620px;
    font-family: "Cinzel", serif;
    font-weight: 600;
    font-size: 120px;
    line-height: 1.05;
    text-align: center;
    color: var(--faint);
    letter-spacing: 4px;
  }
  .brand {
    position: absolute;
    left: 74px;
    top: 66px;
    width: 196px;
    height: 240px;
    display: flex;
    flex-direction: column;
    align-items: center;
    justify-content: center;
    gap: 14px;
  }
  .brand-square {
    width: 110px;
    height: 110px;
    background: var(--ink);
  }
  .brand-name {
    font-family: "Cinzel", serif;
    font-weight: 600;
    font-size: 26px;
    line-height: 1.1;
    text-align: center;
    color: var(--ink);
  }
  .label {
    position: absolute;
    font-family: "Alfa Slab One", serif;
    color: var(--ink);
    display: flex;
    align-items: center;
    gap: 8px;
    line-height: 1;
    letter-spacing: 0.5px;
  }
  .label svg { flex: none; }
  .label-recipe { left: 312px; top: 64px; font-size: 50px; }
  .label-ingredients { left: 286px; top: 258px; font-size: 25px; }
  .label-instructions { left: 72px; top: 481px; font-size: 25px; }
  .write-line {
    position: absolute;
    right: 84px;
    height: 0;
    border-bottom: 2px dotted var(--rule);
  }
  .site {
    position: absolute;
    right: 52px;
    top: 864px;
    font-family: "Poppins", sans-serif;
    font-size: 18px;
    color: var(--ink);
  }
</style>
</head>
<body>
<div class="card">
  <div class="backdrop-name" aria-hidden="true">BRAMBLE FORK COOKWARE</div>

  <div class="cut-border"></div>

  <div class="brand">
    <div class="brand-square"></div>
    <div class="brand-name">Bramble Fork Cookware</div>
  </div>

  <div class="label label-recipe">
    <svg width="30" height="30" viewBox="0 0 20 20" aria-hidden="true"><path d="M3 3 L17 17 M17 3 L3 17" stroke="#111" stroke-width="2.4" stroke-linecap="round"/></svg>
    RECIPE
  </div>
  <div class="write-line" style="left:546px; top:108px;"></div>
  <div class="write-line" style="left:358px; top:190px;"></div>

  <div class="label label-ingredients">
    <svg width="18" height="18" viewBox="0 0 20 20" aria-hidden="true"><path d="M3 3 L17 17 M17 3 L3 17" stroke="#111" stroke-width="2.6" stroke-linecap="round"/></svg>
    INGREDIENTS
  </div>
  <div class="write-line" style="left:512px; top:276px;"></div>
  <div class="write-line" style="left:96px; top:368px;"></div>
  <div class="write-line" style="left:96px; top:432px;"></div>

  <div class="label label-instructions">
    <svg width="18" height="18" viewBox="0 0 20 20" aria-hidden="true"><path d="M3 3 L17 17 M17 3 L3 17" stroke="#111" stroke-width="2.6" stroke-linecap="round"/></svg>
    INSTRUCTIONS
  </div>
  <div class="write-line" style="left:290px; top:500px;"></div>
  <div class="write-line" style="left:86px; top:570px;"></div>
  <div class="write-line" style="left:86px; top:638px;"></div>
  <div class="write-line" style="left:86px; top:706px;"></div>
  <div class="write-line" style="left:86px; top:774px;"></div>
  <div class="write-line" style="left:86px; top:842px;"></div>

  <div class="site">www.brambleforkcookware.com</div>
</div>
</body>
</html>
```